Design a compelling Tarnwove Business Card that will drive people to my site

I want a business card that I can give to people—less to tell them who I am and more to direct them to my website. My website is a portal for Pelmor Aquatics Officials and a place for people who want to become Pelmor Aquatics Officials.
I am uploading my official company logo as well as a business card mockup that I did on my own. Please feel free to completely stray from this design.
I've included a screen recording of the homepage of my website as well.
Target Market(s)
Pelmor Aquatics Officials and people who desire to become one
Contact Information for Business Card
website url
Look and feel
Each slider illustrates characteristics of the customer's brand and the style your logo design should communicate.

```html
<!DOCTYPE html>
<html lang="en">
<head>
<meta charset="utf-8">
<title>Tarnwove Business Card</title>
<link rel="stylesheet" href="https://fonts.googleapis.com/css2?family=Poppins:wght@400;500;700&display=swap">
<style>
  :root {
    --brand-blue: #3a52a6;
    --soft-blue: #8fa6dc;
    --paper: #ffffff;
    --page: #eceef3;
  }
  * { margin: 0; padding: 0; box-sizing: border-box; }
  html, body {
    width: 1186px; height: 1200px; overflow: hidden;
    background: var(--page);
    font-family: "Poppins", sans-serif;
  }
  .card {
    position: absolute; left: 163px; width: 860px; height: 491px;
    background: var(--brand-blue); overflow: hidden;
    box-shadow: 0 6px 18px rgba(0,0,0,0.18);
  }
  .card--front { top: 70px; }
  .card--back { top: 639px; }

  .card__artwork {
    position: absolute; left: 0; right: 0; top: 190px; height: 180px;
    background: linear-gradient(180deg, var(--brand-blue) 0%, var(--soft-blue) 100%);
  }
  .card__contact-panel {
    position: absolute; left: 0; right: 0; bottom: 0; height: 121px;
    background: var(--paper);
  }

  .wordmark {
    position: absolute; color: var(--paper); font-weight: 500;
    letter-spacing: -1px; line-height: 1;
  }
  .card--front .wordmark { left: 38px; top: 36px; font-size: 80px; }

  .person { position: absolute; right: 42px; top: 30px; text-align: right; }
  .person__name { color: var(--soft-blue); font-weight: 700; font-size: 29px; line-height: 1.15; }
  .person__title { color: var(--paper); font-size: 22px; line-height: 1.3; }
  .person__tab {
    position: absolute; right: -10px; top: 40px; width: 22px; height: 66px;
    background: var(--paper); border-radius: 10px 0 0 10px;
  }

  .contact {
    position: absolute; right: 30px; bottom: 14px; list-style: none;
    text-align: right; color: var(--brand-blue); font-size: 24px; line-height: 1.28;
  }
  .contact li { display: flex; justify-content: flex-end; align-items: center; gap: 10px; }
  .contact svg { width: 16px; height: 16px; fill: var(--soft-blue); }

  .card--back .wordmark {
    left: 0; right: 0; top: 170px; text-align: center; font-size: 110px;
  }
  .tagline {
    position: absolute; left: 130px; right: 130px; top: 323px; height: 50px;
    background: linear-gradient(90deg, rgba(143,166,220,0) 0%, rgba(143,166,220,0.55) 50%, rgba(143,166,220,0) 100%);
    color: var(--paper); font-size: 26px; text-align: center; line-height: 50px;
  }
</style>
</head>
<body>

<section class="card card--front">
  <div class="card__artwork" role="img" aria-label="Flowing water wave artwork in light and dark blue"></div>
  <div class="card__contact-panel"></div>

  <div class="wordmark">tarnwove</div>

  <div class="person">
    <div class="person__name">Marcus Velleran</div>
    <div class="person__title">CEO &amp; Founder</div>
  </div>
  <span class="person__tab"></span>

  <ul class="contact">
    <li>(555) 201-4417
      <svg viewBox="0 0 16 16"><path d="M3 2h3l1.5 3.5-2 1.2a8 8 0 0 0 3.8 3.8l1.2-2L14 10v3a1 1 0 0 1-1 1A11 11 0 0 1 2 3a1 1 0 0 1 1-1z"/></svg>
    </li>
    <li>marcus@tarnwove.com
      <svg viewBox="0 0 16 16"><path d="M1 4h14v9H1z M1 4l7 5 7-5" stroke="var(--paper)" stroke-width="1"/></svg>
    </li>
    <li>www.tarnwove.com
      <svg viewBox="0 0 16 16"><circle cx="8" cy="8" r="7"/><path d="M1 8h14M8 1c3 3 3 11 0 14M8 1c-3 3-3 11 0 14" stroke="var(--paper)" stroke-width="1" fill="none"/></svg>
    </li>
  </ul>
</section>

<section class="card card--back">
  <div class="wordmark">tarnwove</div>
  <div class="tagline">The Poolside Judges’ Home Base</div>
</section>

</body>
</html>
```